Business Card Design Project

We have recently completed CraftHive projects for a new logo and wesbite.
We now require new business cards.
We hand out very little printed material to clients as all information is online. When we do hand out something, like a business card, we want it to have real impact and make a statement about the quality and professionalism of our company.
We have an idea of what we want our card to look like but we want a designer to make sure they have impact and look great.
Our requirements are…
Size: 85mm X 55mm - Landscape
Front of card: Logo plus the following contact information.
Dennis Marlow
Operations Manager
Phone +44(0) 1632 xxx xxx
Mobile +44(0) 7700 xxx xxx
Email denmo@korvantix.example
Address 17 Pellick Row, Aberdeen AB12 9QZ
Website www.korvantix.example
How you layout the front of the card is up to you, we would like to see some different ideas. Attached are two versions of our logo that may be used.
Back of card: We would like this to be simple but again have impact. Our current thought is to have the logo or just the large W design from the logo in white against a dark background, perhaps made up from the dark green in the logo.
The logos are attached so you can see the colours in them but the dark ones are..
Dark Blue = C:88, M:55, Y:44, K:28
Dark Green = C:87, M:53, Y:50, K:50
We sometimes also use a bright orange as an accent or highlight colour…
Orange: = C:0, M:39, Y:94, K:0

```html
<!DOCTYPE html>
<html lang="en">
<head>
<meta charset="utf-8">
<title>Korvantix Systems – Business Card Concepts</title>
<link rel="stylesheet" href="https://fonts.googleapis.com/css2?family=Open+Sans:wght@400;600;700&display=swap">
<style>
  :root {
    --stage: #e8e5e0;
    --label: #2a2624;
    --card: #ffffff;
    --ink-dark: #1b4a52;
    --ink-body: #2d3436;
    --ink-muted: #3d6e7a;
    --band-dark: #1d5157;
    --band-light-a: #3f7c84;
    --band-light-b: #78adb2;
    --back-dark: #163f45;
    --back-mark: #4f878d;
    --accent: #f5a01a;
  }
  * { box-sizing: border-box; margin: 0; padding: 0; }
  html, body { width: 1200px; height: 788px; overflow: hidden; }
  body {
    background: var(--stage);
    font-family: "Open Sans", Arial, sans-serif;
    position: relative;
  }
  .sheet-label {
    position: absolute;
    font-size: 21px;
    color: var(--label);
    transform: translateX(-50%);
    line-height: 1;
  }
  .card {
    position: absolute;
    width: 502px;
    height: 325px;
    border-radius: 22px;
    background: var(--card);
    overflow: hidden;
    box-shadow: 0 6px 14px rgba(0,0,0,.22);
  }
  .card--front { left: 85px; top: 57px; }
  .card--back-light { left: 626px; top: 54px; }
  .card--back-dark { left: 65px; top: 444px; background: var(--back-dark); border-radius: 24px; }
  .card--back-stacked { left: 626px; top: 444px; }

  .wordmark {
    position: absolute;
    font-weight: 700;
    color: var(--ink-dark);
    letter-spacing: 2px;
    white-space: nowrap;
    line-height: 1;
  }
  .card--front .wordmark { left: 56px; top: 70px; font-size: 30px; }
  .card--back-light .wordmark {
    left: 0; right: 0; top: 150px; text-align: center; font-size: 30px;
  }
  .card--back-stacked .wordmark {
    left: 0; right: 0; top: 205px; text-align: center; font-size: 32px; letter-spacing: 1.5px;
  }
  .card--back-dark .wordmark {
    left: 0; right: 0; top: 136px; text-align: center; font-size: 54px;
    color: var(--back-mark); letter-spacing: 4px;
  }
  .wordmark-dot {
    display: inline-block;
    width: 13px; height: 13px;
    border-radius: 50%;
    background: var(--accent);
    margin-right: 12px;
    vertical-align: middle;
    position: relative; top: -3px;
  }

  .person { position: absolute; left: 103px; top: 152px; }
  .person-name { font-size: 17px; font-weight: 700; color: var(--ink-dark); }
  .person-role { font-size: 12.5px; color: var(--ink-muted); margin-top: 1px; }

  .contact {
    position: absolute; left: 307px; top: 151px;
    font-size: 12.5px; color: var(--ink-body); line-height: 1;
  }
  .contact-line { height: 24px; }
  .contact-key { font-weight: 700; font-style: italic; }
  .address { line-height: 18px; }

  .bands { position: absolute; left: 0; top: 0; }
  .band-text {
    position: absolute; color: #fff; font-size: 12.5px; white-space: nowrap;
  }
  .band-text--web { left: 50px; top: 255px; }
  .band-text--email { left: 307px; top: 273px; }

  .site-url {
    position: absolute; left: 0; right: 0; text-align: center;
    font-size: 17px; color: var(--ink-dark); letter-spacing: 3.5px;
  }
  .card--back-light .site-url { top: 284px; }
  .card--back-stacked .site-url { top: 280px; }
</style>
</head>
<body>
  <span class="sheet-label" style="left:320px; top:22px;">Front</span>
  <span class="sheet-label" style="left:896px; top:22px;">Back - 1</span>
  <span class="sheet-label" style="left:323px; top:405px;">Back - 2</span>
  <span class="sheet-label" style="left:896px; top:405px;">Back - 3</span>

  <section class="card card--front">
    <div class="wordmark"><span class="wordmark-dot"></span>KORVANTIX SYSTEMS</div>

    <div class="person">
      <div class="person-name">Dennis Marlow</div>
      <div class="person-role">Operations Manager</div>
    </div>

    <div class="contact">
      <div class="contact-line"><span class="contact-key">c</span> : +44(0) 7700 xxx xxx</div>
      <div class="contact-line"><span class="contact-key">p</span> : +44(0) 1632 xxx xxx</div>
      <div class="address">17 Pellick Row<br>Aberdeen AB12 9QZ</div>
    </div>

    <svg class="bands" width="502" height="325" viewBox="0 0 502 325" aria-hidden="true">
      <defs>
        <linearGradient id="bandLight" x1="0" y1="0" x2="1" y2="0">
          <stop offset="0" stop-color="var(--band-light-a)"/>
          <stop offset="1" stop-color="var(--band-light-b)"/>
        </linearGradient>
      </defs>
      <polygon points="0,248 10,250 290,250 262,284 0,284" fill="rgba(0,0,0,.12)"/>
      <polygon points="0,244 293,244 262,280 0,280" fill="var(--band-dark)"/>
      <polygon points="262,266 502,266 502,302 232,302" fill="rgba(0,0,0,.15)"/>
      <polygon points="263,262 502,262 502,298 233,298" fill="url(#bandLight)"/>
    </svg>
    <span class="band-text band-text--web">www.korvantix.example</span>
    <span class="band-text band-text--email">denmo@korvantix.example</span>
  </section>

  <section class="card card--back-light">
    <div class="wordmark"><span class="wordmark-dot"></span>KORVANTIX SYSTEMS</div>
    <div class="site-url">www.korvantix.example</div>
  </section>

  <section class="card card--back-dark">
    <div class="wordmark">KORVANTIX</div>
  </section>

  <section class="card card--back-stacked">
    <div class="wordmark">KORVANTIX SYSTEMS</div>
    <div class="site-url">www.korvantix.example</div>
  </section>
</body>
</html>
```